Stationery and Business Card Design

We need stationary design for our new company lanternfold. Lanternfold is a company that provides city apartment rentals for tourists in Athens We need business cards, letterheads for A4 and A5 and envelopes for A4 A5. The design needs to be modern, friendly and corporate.

Target Market(s)

City Tourists

Industry/Entity Type

Tourism

```html
<!DOCTYPE html>
<html lang="en">
<head>
<meta charset="utf-8">
<title>Lanternfold Apartment — Business Card</title>
<link rel="stylesheet" href="https://fonts.googleapis.com/css2?family=Montserrat:wght@400;600;700&display=swap">
<style>
  :root {
    --backdrop: #8e0a56;
    --card-dark: #2b2a2b;
    --accent: #8c1861;
    --paper: #f3efee;
    --blush: #ead6df;
    --ink: #2b2a2b;
    --light-text: #f4eef1;
  }
  * { box-sizing: border-box; margin: 0; padding: 0; }
  html, body { width: 1200px; height: 900px; overflow: hidden; }
  body {
    background: var(--backdrop);
    font-family: "Montserrat", sans-serif;
    position: relative;
  }
  .card {
    position: absolute;
    left: 320px;
    width: 560px;
    height: 320px;
    overflow: hidden;
    box-shadow: 0 6px 18px rgba(0,0,0,0.25);
  }
  .card-front { top: 90px; background: var(--card-dark); }
  .card-back { top: 490px; background: var(--paper); }

  /* Front */
  .brand-square {
    position: absolute;
    width: 74px; height: 74px;
    background: var(--accent);
  }
  .card-front .brand-square { left: 243px; top: 70px; }
  .brand-rule {
    position: absolute;
    left: 0; right: 0; top: 178px;
    height: 3px;
    background: var(--accent);
  }
  .brand-name {
    position: absolute;
    left: 50%; top: 163px;
    transform: translateX(-50%);
    padding: 0 14px;
    background: var(--card-dark);
    color: var(--light-text);
    font-size: 17px;
    letter-spacing: 1.5px;
    white-space: nowrap;
  }
  .web-band {
    position: absolute;
    left: 0; right: 0; bottom: 0;
    height: 58px;
    background: var(--accent);
    color: var(--light-text);
    font-size: 14px;
    text-align: center;
    line-height: 58px;
    letter-spacing: 0.5px;
  }

  /* Back */
  .back-panel {
    position: absolute;
    left: 0; top: 0; bottom: 0;
    width: 170px;
    background: var(--card-dark);
  }
  .back-strip {
    position: absolute;
    left: 170px; top: 0; bottom: 0;
    width: 22px;
    background: var(--accent);
  }
  .card-back .brand-square { left: 48px; top: 123px; }
  .blush-block {
    position: absolute;
    left: 230px; top: 42px;
    width: 250px; height: 240px;
    background: var(--blush);
  }
  .holder {
    position: absolute;
    right: 34px; top: 40px;
    text-align: right;
    color: var(--ink);
  }
  .holder-name { font-size: 15px; font-weight: 700; letter-spacing: 0.5px; }
  .holder-role { font-size: 10px; color: var(--accent); font-weight: 600; }
  .contact-list {
    position: absolute;
    left: 238px; top: 118px;
    list-style: none;
  }
  .contact-item {
    display: flex;
    align-items: center;
    gap: 12px;
    margin-bottom: 14px;
  }
  .contact-icon {
    width: 26px; height: 26px;
    background: var(--card-dark);
    display: flex; align-items: center; justify-content: center;
    flex-shrink: 0;
  }
  .contact-text {
    font-size: 9px;
    line-height: 14px;
    color: var(--ink);
    letter-spacing: 0.8px;
    text-transform: uppercase;
  }
</style>
</head>
<body>
  <section class="card card-front" aria-label="Business card front">
    <div class="brand-square"></div>
    <div class="brand-rule"></div>
    <div class="brand-name">LANTERNFOLD APARTMENT</div>
    <div class="web-band">www.lanternfoldaprtmt.com</div>
  </section>

  <section class="card card-back" aria-label="Business card back">
    <div class="back-panel"></div>
    <div class="back-strip"></div>
    <div class="brand-square"></div>
    <div class="blush-block"></div>
    <div class="holder">
      <p class="holder-name">MR. KALO</p>
      <p class="holder-role">CEO</p>
    </div>
    <ul class="contact-list">
      <li class="contact-item">
        <span class="contact-icon">
          <svg width="14" height="14" viewBox="0 0 24 24" aria-hidden="true"><path fill="#fff" d="M6.6 10.8a15 15 0 0 0 6.6 6.6l2.2-2.2c.3-.3.7-.4 1-.2 1.1.4 2.3.6 3.6.6.6 0 1 .4 1 1V20c0 .6-.4 1-1 1A17 17 0 0 1 3 4c0-.6.4-1 1-1h3.5c.6 0 1 .4 1 1 0 1.3.2 2.5.6 3.6.1.3 0 .7-.2 1z"/></svg>
        </span>
        <span class="contact-text">+30 210 555 0147<br>+30 210 555 0182</span>
      </li>
      <li class="contact-item">
        <span class="contact-icon">
          <svg width="14" height="14" viewBox="0 0 24 24" aria-hidden="true" fill="none" stroke="#fff" stroke-width="2"><circle cx="12" cy="12" r="9"/><path d="M3 12h18M12 3c3 3 3 15 0 18M12 3c-3 3-3 15 0 18"/></svg>
        </span>
        <span class="contact-text">hello@lanternfold.com<br>stay.lanternfold.com</span>
      </li>
      <li class="contact-item">
        <span class="contact-icon">
          <svg width="14" height="14" viewBox="0 0 24 24" aria-hidden="true"><path fill="#fff" d="M12 2a7 7 0 0 0-7 7c0 5 7 13 7 13s7-8 7-13a7 7 0 0 0-7-7zm0 9.5A2.5 2.5 0 1 1 12 6.5a2.5 2.5 0 0 1 0 5z"/></svg>
        </span>
        <span class="contact-text">14 Ermou Street<br>Athens 105 63</span>
      </li>
    </ul>
  </section>
</body>
</html>
```